VENTURE CAPITAL GROUP BUSINESS CARD DESIGN

Venture Capital Group based in SF looking for a bold business card design. No trendy colour explosion, 3D effects etc. Just "simple" optical effects. Works on your brain, keeps your eye focused and sticks to your mind.
Target Market(s)
Technology startups
Industry/Entity Type
Venture Capital
Contact Information for Business Card
DESMOND WHITLAKE
MANAGING PARTNER
187 FENWORTH ST SAN FRANCISCO, CA 94187
415.555.0142 O
415.555.0147 F
415.555.0193 C
desmond@veldtmoorcapital.ventures

```html
<!DOCTYPE html>
<html lang="en">
<head>
<meta charset="utf-8">
<title>Veldtmoor Capital Group – Business Card</title>
<link href="https://fonts.googleapis.com/css2?family=Open+Sans:wght@400;600;700;800&display=swap" rel="stylesheet">
<style>
  :root {
    --green-dark: #0f5a24;
    --green-mid: #1d8a35;
    --green-light: #3cbf3f;
    --ink: #1c3d22;
    --grey-soft: #e4e4e4;
    --grey-edge: #b9b9b9;
    --paper: #ffffff;
    --backdrop: #dcdfdc;
  }
  * { box-sizing: border-box; margin: 0; padding: 0; }
  html, body { width: 1200px; height: 900px; overflow: hidden; }
  body {
    background: var(--backdrop);
    font-family: "Open Sans", Arial, sans-serif;
    position: relative;
  }
  .card {
    position: absolute;
    left: 270px;
    width: 660px;
    height: 377px;
    background: var(--paper);
    border-radius: 22px;
    overflow: hidden;
    box-shadow: 0 6px 18px rgba(0,0,0,.18);
  }
  .card--front { top: 50px; }
  .card--back { top: 473px; }
  .card__bands { position: absolute; inset: 0; width: 100%; height: 100%; }

  .brand {
    position: absolute;
    display: flex;
    align-items: center;
    gap: 14px;
  }
  .brand__dot {
    width: 46px; height: 46px; border-radius: 50%;
    background: radial-gradient(circle at 35% 30%, #ffffff, var(--grey-soft) 60%, var(--grey-edge));
    flex: none;
  }
  .brand__name {
    font-weight: 600;
    color: var(--green-dark);
    letter-spacing: 1.5px;
    white-space: nowrap;
  }
  .card--front .brand { left: 50%; top: 140px; transform: translateX(-50%); }
  .card--front .brand__name { font-size: 26px; }
  .card--back .brand { left: 40px; top: 48px; }
  .card--back .brand__dot { width: 38px; height: 38px; }
  .card--back .brand__name { font-size: 17px; }

  .person {
    position: absolute;
    right: 40px;
    top: 104px;
    text-align: right;
  }
  .person__name {
    font-size: 24px; font-weight: 800; color: var(--green-dark); letter-spacing: 1px;
  }
  .person__title {
    font-size: 12px; font-weight: 600; color: var(--green-light); letter-spacing: 1px;
    border-bottom: 1.5px solid var(--green-mid);
    padding-bottom: 2px;
  }
  .rule {
    position: absolute;
    left: 40px; right: 40px; top: 176px;
    height: 1.5px; background: var(--green-dark);
  }
  .contact {
    position: absolute;
    left: 40px; top: 196px;
    font-size: 13.5px; color: var(--ink); line-height: 1.32;
    list-style: none;
  }
  .contact__address { font-weight: 600; margin-bottom: 4px; }
  .contact li { display: flex; align-items: center; gap: 8px; padding-left: 18px; }
  .contact li svg { width: 12px; height: 12px; fill: var(--green-light); flex: none; }
</style>
</head>
<body>

<section class="card card--front" aria-label="Card front">
  <svg class="card__bands" viewBox="0 0 660 377" preserveAspectRatio="none" aria-hidden="true">
    <polygon points="0,377 0,362 330,362 360,344 660,330 660,377" fill="var(--green-light)"/>
    <polygon points="0,377 0,318 290,318 345,346 345,377" fill="var(--green-dark)"/>
  </svg>
  <div class="brand">
    <span class="brand__dot"></span>
    <span class="brand__name">VELDTMOOR CAPITAL GROUP</span>
  </div>
</section>

<section class="card card--back" aria-label="Card back">
  <svg class="card__bands" viewBox="0 0 660 377" preserveAspectRatio="none" aria-hidden="true">
    <polygon points="0,377 0,368 460,300 660,300 660,377" fill="var(--green-light)"/>
    <polygon points="0,377 0,372 480,306 660,306 660,377" fill="var(--paper)"/>
    <polygon points="660,377 660,356 0,377" fill="var(--green-mid)"/>
    <polygon points="530,228 660,214 660,286 500,304" fill="var(--green-dark)"/>
  </svg>

  <div class="brand">
    <span class="brand__dot"></span>
    <span class="brand__name">VELDTMOOR CAPITAL GROUP</span>
  </div>

  <div class="person">
    <p class="person__name">DESMOND WHITLAKE</p>
    <p class="person__title">MANAGING PARTNER</p>
  </div>

  <div class="rule"></div>

  <ul class="contact">
    <p class="contact__address">187 FENWORTH ST SAN<br>FRANCISCO, CA 94187</p>
    <li><svg viewBox="0 0 12 12"><path d="M2.5 1l2 2.2-1 1.3c.7 1.5 2 2.8 3.5 3.5l1.3-1 2.2 2-1.2 1.8C5 10.6 1.4 7 .8 2.2z"/></svg>415.555.0142</li>
    <li><svg viewBox="0 0 12 12"><rect x="3" y="1" width="6" height="3"/><rect x="1" y="5" width="10" height="4" rx="1"/><rect x="3" y="9" width="6" height="2"/></svg>415.555.0147</li>
    <li><svg viewBox="0 0 12 12"><path d="M3.5 0.5h5a1 1 0 0 1 1 1v9a1 1 0 0 1-1 1h-5a1 1 0 0 1-1-1v-9a1 1 0 0 1 1-1zM4 2v7h4V2z"/></svg>415.555.0193</li>
    <li><svg viewBox="0 0 12 12"><path d="M1 2.5h10v7H1zM2 3.5l4 3 4-3v-.2H2z" fill-rule="evenodd"/></svg>desmond@veldtmoorcapital.ventures</li>
  </ul>
</section>

</body>
</html>
```